KLV Plant Services

We are a heavy diesel mechanical business with additional air con certificates, remapping engine rebuilt

Contact Information for Business Card

Company Name, Director Name, Managing Director, Contact details, email and website

Font styles to use
Serif
Script

```html
<!DOCTYPE html>
<html lang="en">
<head>
<meta charset="utf-8">
<title>KLV Plant Services – Business Card</title>
<link href="https://fonts.googleapis.com/css2?family=Noto+Serif:wght@400;700&display=swap" rel="stylesheet">
<style>
  :root {
    --navy: #29286f;
    --ink: #111111;
    --text: #2b2b2b;
    --paper: #ffffff;
    --backdrop: #3b3b3b;
  }
  * { box-sizing: border-box; margin: 0; padding: 0; }
  html, body { width: 1200px; height: 780px; overflow: hidden; }
  body {
    background: var(--backdrop);
    font-family: "Noto Serif", Georgia, serif;
    position: relative;
  }
  .card {
    position: absolute;
    top: 235px;
    width: 520px;
    height: 310px;
    background: var(--paper);
    border-radius: 18px;
    overflow: hidden;
    box-shadow: 0 10px 28px rgba(0,0,0,.45);
  }
  .card--details { left: 50px; }
  .card--front { left: 630px; }

  .wave { position: absolute; inset: 0; width: 100%; height: 100%; }

  .brand {
    color: var(--navy);
    font-weight: 700;
    line-height: 1.1;
    text-align: center;
  }
  .card--details .brand {
    position: absolute;
    left: 40px; top: 58px;
    width: 190px;
    font-size: 26px;
  }
  .card--front .brand {
    position: absolute;
    left: 0; right: 0; top: 108px;
    font-size: 40px;
  }
  .brand__dot {
    display: block;
    width: 14px; height: 14px;
    margin: 0 auto 10px;
    border-radius: 50%;
    background: var(--navy);
  }

  .divider {
    position: absolute;
    left: 262px; top: 40px;
    width: 1px; height: 180px;
    background: var(--navy);
  }

  .contact {
    position: absolute;
    left: 282px; top: 38px;
    color: var(--text);
  }
  .contact__name {
    color: var(--navy);
    font-weight: 700;
    font-size: 21px;
    letter-spacing: .5px;
    text-transform: uppercase;
  }
  .contact__role {
    color: var(--navy);
    font-size: 15px;
    margin-bottom: 10px;
  }
  .contact__line {
    display: flex; align-items: center; gap: 7px;
    font-size: 15px;
    line-height: 1.45;
  }
  .contact__line svg { width: 12px; height: 12px; flex: none; }
  .contact__address {
    font-size: 15px;
    line-height: 1.4;
    margin-top: 2px;
  }
</style>
</head>
<body>

<section class="card card--details" aria-label="Business card, contact side">
  <svg class="wave" viewBox="0 0 520 310" preserveAspectRatio="none" aria-hidden="true">
    <path d="M0,112 C70,130 150,230 250,262 C320,285 400,296 520,300 L520,310 L0,310 Z" fill="var(--navy)"/>
    <path d="M0,108 C70,126 150,224 250,256 C320,279 400,292 520,296" fill="none" stroke="var(--ink)" stroke-width="4"/>
    <path d="M0,112 C70,130 150,230 250,262 C320,285 400,296 520,300" fill="none" stroke="var(--paper)" stroke-width="2"/>
  </svg>

  <div class="brand"><span class="brand__dot"></span>KLV Plant Services</div>

  <div class="divider"></div>

  <div class="contact">
    <p class="contact__name">Daniel Hart</p>
    <p class="contact__role">Managing Director</p>
    <p class="contact__line">
      <svg viewBox="0 0 12 12"><path d="M3 1 L5 3.5 L4 5 C4.8 6.6 5.6 7.4 7 8 L8.5 7 L11 9 L9.5 11 C5 10.5 1.5 7 1 2.5 Z" fill="var(--navy)"/></svg>
      123 456 789
    </p>
    <p class="contact__line">
      <svg viewBox="0 0 12 12"><rect x="0.5" y="2" width="11" height="8" rx="1" fill="var(--navy)"/><path d="M1 2.5 L6 6.5 L11 2.5" fill="none" stroke="#fff" stroke-width="1"/></svg>
      info@yourgmail.com
    </p>
    <p class="contact__line">
      <svg viewBox="0 0 12 12"><circle cx="6" cy="6" r="5.5" fill="var(--navy)"/><path d="M0.5 6 H11.5 M6 0.5 C3 3 3 9 6 11.5 M6 0.5 C9 3 9 9 6 11.5" fill="none" stroke="#fff" stroke-width=".8"/></svg>
      www.yourwebsite.com
    </p>
    <p class="contact__address">Your address, City<br>State, Zip 1234</p>
  </div>
</section>

<section class="card card--front" aria-label="Business card, front side">
  <div class="brand"><span class="brand__dot"></span>KLV Plant Services</div>
</section>

</body>
</html>
```